Book cover needed for Christian Non-Fiction Book

I need book cover design (eBook , Paperback, and possibly case laminate Hardcover) for use on PQL and Tolvey Press.
Title: Lift Up and Walk
Sub-Title: Bridging Waters and Working in Faithful Hands
Author: Dale Wickens
Also on front cover "Forward by R. Lena Ashford"

I like clean/simple designs. Below are links to examples of covers I like...
https://www.bookvarlo.example/dp/K4821MXQ7T?tag=plinxa-20&linkCode=ogi&th=1&psc=1
https://www.bookvarlo.example/dp/K49HTRZNWA?tag=plinxa-20&linkCode=ogi&th=1&psc=1
https://www.bookvarlo.example/dp/K33WNQ58XE?tag=plinxa-20&linkCode=ogi&th=1&psc=1
https://www.bookvarlo.example/dp/K47R2TVHPD?tag=plinxa-20&linkCode=ogi&th=1&psc=1
https://www.bookvarlo.example/dp/K48M5ZRCUF?tag=plinxa-20&linkCode=ogi&th=1&psc=1
https://www.bookvarlo.example/dp/K31P9LLWHN?tag=plinxa-20&linkCode=ogi&th=1&psc=1

The main idea for Lift Up and Walk is that God is a sending God and being "on the move" or journeying is central to God's character, and therefore God's people. I write about our hesitancy to "go," and how the Bible is full of stories about people "going" from Abraham to Jesus, to the disciples of Jesus.

The core biblical text is the Great Commission in Matthew 28:16-20, where Jesus sends out his followers, though some of them doubt.

This paragraph from the forward by R. Lena Ashford captures the tone of the book well:
This book is a call amid the turmoil. Sacred scripture contains no shortage of narratives in which humans are pulled from their ordinary lives with an inciting incident whose stakes are high. These Biblical figures are lulled from complacency and comfort zones—and yet they are reluctant to serve because they question their ability and influence. Their lessons are relevant for us today: They, and we, are always called and sent with authority. The power of the Holy Spirit equips their “going”—and ours. It’s a sending out that looks less like mastery and more humility. It’s a sending out that is unequivocal service to others modelled in a rabbi-reformer who washed feet and touched the unclean.

I have previously published two shorter books and would be very interested in getting new covers for the old books these so that the three have a similar feel. Whichever designer I go with for "Lift Up and Walk" I would also want to work with on creating a "branded look" for the other two books.

Target Market(s)

Christian, Religion, Spirituality Readers

Requirements
Must have
• The front cover must have this copy...
Lift Up and Walk
Bridging Waters and Working in Faithful Hands
Dale Wickens
Forward by R. Lena Ashford

Must be willing to do the full paperback and/or hardcover, but start with thefront cover please
Nice to have
• See attached files for some book covers I like

```html
<!DOCTYPE html>
<html lang="en">
<head>
<meta charset="utf-8">
<title>Lift Up and Walk — Front Cover</title>
<link rel="stylesheet" href="https://fonts.googleapis.com/css2?family=Cormorant+Garamond:ital,wght@0,500;0,600;1,500&display=swap">
<style>
  :root {
    --backdrop: #d6d5d1;
    --orange-deep: #eba36e;
    --orange-mid: #f3c08a;
    --glow: #fbf3dc;
    --light: #f2f0ec;
    --title-ink: #4c5472;
    --subtitle-ink: #5a3e2e;
  }
  html, body {
    margin: 0;
    padding: 0;
    width: 1200px;
    height: 864px;
    overflow: hidden;
    background: var(--backdrop);
  }
  .canvas {
    position: relative;
    width: 1200px;
    height: 864px;
  }
  .cover {
    position: absolute;
    left: 334px;
    top: 32px;
    width: 533px;
    height: 800px;
    overflow: hidden;
    background:
      radial-gradient(ellipse 62% 42% at 42% 38%, var(--light) 0%, var(--glow) 35%, rgba(251,243,220,0) 72%),
      radial-gradient(ellipse 80% 50% at 35% 22%, #f7dfa6 0%, rgba(247,223,166,0) 70%),
      linear-gradient(180deg, var(--orange-mid) 0%, #f5d9a8 30%, var(--light) 55%, var(--orange-mid) 75%, var(--orange-deep) 100%);
    font-family: "Cormorant Garamond", Garamond, serif;
  }
  .figure-art {
    position: absolute;
    left: 178px;
    top: 150px;
    width: 110px;
    height: 300px;
  }
  .bridge-art {
    position: absolute;
    left: 120px;
    top: 380px;
    width: 413px;
    height: 260px;
  }
  .foreword {
    position: absolute;
    left: 0;
    right: 0;
    top: 74px;
    margin: 0;
    text-align: center;
    font-size: 17px;
    font-weight: 500;
    letter-spacing: 0.06em;
    color: var(--title-ink);
    text-transform: uppercase;
  }
  .title {
    margin: 0;
    font-weight: 600;
    font-size: 80px;
    color: var(--title-ink);
    text-transform: uppercase;
    letter-spacing: 0.01em;
  }
  .title span {
    position: absolute;
    display: block;
    line-height: 90px;
    white-space: nowrap;
  }
  .title .line-1 { left: 62px;  top: 108px; }
  .title .line-2 { left: 150px; top: 228px; }
  .title .line-3 { left: 176px; top: 340px; }
  .subtitle {
    position: absolute;
    margin: 0;
    font-style: italic;
    font-weight: 500;
    font-size: 24px;
    line-height: 30px;
    color: var(--subtitle-ink);
    letter-spacing: 0.02em;
    white-space: nowrap;
  }
  .subtitle-a { left: 132px; top: 200px; }
  .subtitle-b { left: 104px; top: 318px; }
  .author {
    position: absolute;
    right: 36px;
    bottom: 104px;
    margin: 0;
    font-size: 40px;
    font-weight: 500;
    letter-spacing: 0.03em;
    color: var(--title-ink);
    text-transform: uppercase;
  }
</style>
</head>
<body>
<main class="canvas">
  <section class="cover" aria-label="Front cover of Lift Up and Walk">
    <svg class="figure-art" viewBox="0 0 110 300" role="img" aria-label="Silhouette of a person walking into the light">
      <defs>
        <linearGradient id="figureTone" x1="0" y1="0" x2="0" y2="1">
          <stop offset="0" stop-color="#f0c86a" stop-opacity="0.85"/>
          <stop offset="1" stop-color="#f3b45c" stop-opacity="0.75"/>
        </linearGradient>
      </defs>
      <rect x="8" y="0" width="94" height="300" rx="40" fill="url(#figureTone)" opacity="0.7"/>
    </svg>

    <svg class="bridge-art" viewBox="0 0 413 260" role="img" aria-label="Arched footbridge spanning across the light">
      <defs>
        <radialGradient id="bridgeTone" cx="0.6" cy="0.55" r="0.6">
          <stop offset="0" stop-color="#f4c29a" stop-opacity="0.9"/>
          <stop offset="1" stop-color="#f1b787" stop-opacity="0"/>
        </radialGradient>
      </defs>
      <rect x="0" y="0" width="413" height="260" fill="url(#bridgeTone)"/>
    </svg>

    <p class="foreword">Forward by R. Lena Ashford</p>

    <h1 class="title">
      <span class="line-1">Lift Up</span>
      <span class="line-2">and</span>
      <span class="line-3">Walk</span>
    </h1>

    <p class="subtitle subtitle-a">Bridging Waters</p>
    <p class="subtitle subtitle-b">and Working in Faithful Hands</p>

    <p class="author">Dale Wickens</p>
  </section>
</main>
</body>
</html>
```